business card

Business card for new business.
Red and black corporate colors.
Card can have an Indsutrial feel to it. Feel free to add Rust, Bolted steel, or graphics as you see fit. We provide highly specialized services to the below mentioned industries.
Keep information out of corners so that if I want I can choose rounded corners.
Information
- front. name - title - phone - email
- Rear
Welding - Pipe - Fabrication - Rigging - Survey
Kestrel - Dunmore - Port Halloway - Ashcombe - Linvale

```html
<!DOCTYPE html>
<html lang="en">
<head>
<meta charset="utf-8">
<title>Framewell Business Card</title>
<link rel="stylesheet" href="https://fonts.googleapis.com/css2?family=Source+Sans+3:wght@400;700;900&display=swap">
<style>
  :root {
    --backdrop: #2a2a2a;
    --paper: #f4f4f4;
    --ink-dark: #1d1e20;
    --brand-red: #d7111c;
    --steel-grey: #7a7a7a;
    --text-grey: #5e5e5e;
    --silver: #d9d9d9;
    --white: #ffffff;
  }
  * { box-sizing: border-box; margin: 0; padding: 0; }
  html, body {
    width: 1200px;
    height: 960px;
    overflow: hidden;
    background: var(--backdrop);
    font-family: "Source Sans 3", Arial, sans-serif;
  }
  .canvas { position: relative; width: 1200px; height: 960px; }

  .card {
    position: absolute;
    width: 600px;
    height: 343px;
    box-shadow: 0 3px 8px rgba(0, 0, 0, 0.55);
  }
  .card--front { left: 302px; top: 124px; background: var(--paper); }
  .card--back { left: 300px; top: 493px; background: var(--ink-dark); }

  .holder {
    position: absolute;
    right: 43px;
    top: 41px;
    text-align: right;
    line-height: 22px;
  }
  .holder__name {
    color: var(--brand-red);
    font-weight: 700;
    font-size: 21px;
  }
  .holder__title {
    color: var(--text-grey);
    font-size: 16px;
    letter-spacing: 0.3px;
  }
  .accent-bar {
    position: absolute;
    width: 13px;
    height: 40px;
  }
  .accent-bar--red { right: 0; top: 43px; background: var(--brand-red); }
  .accent-bar--grey { left: 0; top: 248px; height: 54px; width: 12px; background: var(--steel-grey); }

  .wordmark {
    position: absolute;
    left: 0;
    width: 100%;
    display: flex;
    align-items: center;
    justify-content: center;
    gap: 12px;
    font-weight: 900;
    line-height: 1;
  }
  .wordmark__square { width: 14px; height: 14px; background: var(--brand-red); }
  .card--front .wordmark { top: 140px; font-size: 46px; color: var(--steel-grey); }
  .card--back .wordmark { top: 133px; font-size: 56px; color: var(--silver); }

  .contact-list {
    position: absolute;
    left: 44px;
    top: 246px;
    list-style: none;
    font-size: 16px;
    color: var(--text-grey);
    line-height: 19.5px;
  }
  .contact-list li { display: flex; align-items: center; gap: 7px; }
  .contact-list svg { width: 15px; height: 15px; flex: none; }

  .services {
    position: absolute;
    left: 0;
    top: 254px;
    width: 100%;
    text-align: center;
    color: var(--white);
    font-size: 16px;
    line-height: 19.5px;
  }
  .services .dot { color: var(--brand-red); font-size: 11px; vertical-align: 1px; }
</style>
</head>
<body>
<main class="canvas">
  <section class="card card--front" aria-label="Card front">
    <div class="holder">
      <p class="holder__name">MARA QUILL</p>
      <p class="holder__title">PRESIDENT</p>
    </div>
    <span class="accent-bar accent-bar--red"></span>

    <div class="wordmark">
      <span>FRAMEWELL</span>
      <span class="wordmark__square"></span>
    </div>

    <span class="accent-bar accent-bar--grey"></span>
    <ul class="contact-list">
      <li>
        <svg viewBox="0 0 16 16" aria-hidden="true"><path fill="#d7111c" d="M2 6c0-2 3-3.5 6-3.5S14 4 14 6l-3 1-.6-1.6H5.6L5 7 2 6zm2.5 2h7l1.5 5.5H3L4.5 8zM8 9a2 2 0 1 0 0 4 2 2 0 0 0 0-4z"/></svg>
        <span>555 0142 7781</span>
      </li>
      <li>
        <svg viewBox="0 0 16 16" aria-hidden="true"><rect x="1.5" y="3.5" width="13" height="9" fill="#d7111c"/><path d="M1.5 3.8 8 9l6.5-5.2" stroke="#f4f4f4" stroke-width="1.3" fill="none"/></svg>
        <span>mara@framewell.com</span>
      </li>
      <li>
        <svg viewBox="0 0 16 16" aria-hidden="true"><circle cx="8" cy="8" r="6.5" fill="#d7111c"/><path d="M5 5.5c1.5-.5 2 .8 3 .6.8 1 .2 2-1 2.2-.4 1.2-.8 2.3-1.5 2.7M10 9.5c.8.2 1.3 1 1 2" stroke="#f4f4f4" stroke-width="1.2" fill="none"/></svg>
        <span>www.framewell.com</span>
      </li>
    </ul>
  </section>

  <section class="card card--back" aria-label="Card back">
    <div class="wordmark">
      <span>FRAMEWELL</span>
    </div>
    <p class="services">
      Welding <span class="dot">•</span> Pipe <span class="dot">•</span> Fabrication <span class="dot">•</span> Rigging<br>
      Survey <span class="dot">•</span> Kestrel <span class="dot">•</span> Dunmore <span class="dot">•</span> Port Halloway<br>
      Ashcombe <span class="dot">•</span> Linvale
    </p>
  </section>
</main>
</body>
</html>
```